Communications Consultancy needs Print Design Project

We are a communications consultancy providing training and services for organisations and individuals.

We have developed a Project Communication Strategy Model that is sound in functionality but poor in graphical design and structure.

We need to create a single page document that is a practical and profession tool to guide Project Managers through the process of communicating project outcomes.

The model will be used as a hard copy resource and will also need to be replicated onto a PowerPoint slide for instructional purposes.

Target Market(s)

Project Management Professionals

Industry/Entity Type

Communications

Requirements
Must have
• Icons to represent the different communication mediums (icons shown in attachment are just for example)

Enable future editing and be transfereable to PowerPoint

Have the company Logo (this can be privided as vector file etc.

Company contact details, website, phone, ABN etc.

```html
<!DOCTYPE html>
<html lang="en">
<head>
<meta charset="utf-8">
<title>Project Communication Strategy Model</title>
<link rel="stylesheet" href="https://fonts.googleapis.com/css2?family=Mulish:wght@400;600;700;800&display=swap">
<style>
  :root {
    --green: #95bf3c;
    --dark: #333333;
    --ink: #231f20;
    --cell-grey: #f1f1f3;
    --rule: #8a8a8a;
    --white: #ffffff;
  }
  * { box-sizing: border-box; margin: 0; padding: 0; }
  html, body { width: 1200px; height: 848px; overflow: hidden; background: var(--white); }
  body { font-family: "Mulish", Arial, sans-serif; color: var(--dark); }
  .canvas { position: relative; width: 1200px; height: 848px; overflow: hidden; background: var(--white); }

  .title-tab {
    position: absolute; left: 0; top: 40px; width: 410px; height: 43px;
    background: var(--green); color: var(--dark);
    font-size: 17px; font-weight: 600; line-height: 43px; padding-left: 34px;
  }
  .brand {
    position: absolute; right: 34px; top: 40px;
    display: flex; align-items: center; gap: 12px;
  }
  .brand-mark { width: 18px; height: 18px; background: var(--green); }
  .brand-name { font-size: 54px; font-weight: 800; color: var(--dark); letter-spacing: -1.5px; line-height: 1; }

  .connectors { position: absolute; left: 0; top: 0; width: 1200px; height: 848px; }

  .flow-box {
    position: absolute; background: var(--dark); color: var(--white);
    border-radius: 4px; text-align: center; font-weight: 600;
  }
  .flow-event { left: 494px; top: 117px; width: 203px; height: 38px; line-height: 38px; font-size: 19px; }
  .flow-yes { left: 416px; top: 211px; width: 81px; height: 40px; line-height: 40px; font-size: 14px; }
  .flow-no { left: 677px; top: 211px; width: 81px; height: 40px; line-height: 40px; font-size: 14px; }
  .flow-end { left: 839px; top: 211px; width: 80px; height: 40px; line-height: 40px; font-size: 14px; }
  .flow-question { position: absolute; left: 530px; top: 172px; width: 132px; text-align: center; font-size: 13px; font-weight: 700; color: var(--ink); }

  .section-bar {
    position: absolute; top: 282px; height: 40px; background: var(--green);
    border-radius: 5px; text-align: center; line-height: 40px;
    font-size: 19px; color: var(--dark);
  }
  .bar-channel { left: 28px; width: 226px; }
  .bar-medium { left: 289px; width: 483px; }
  .bar-delivery { left: 805px; width: 362px; }

  .sub-pill {
    position: absolute; top: 341px; height: 30px; background: var(--green);
    border-radius: 4px; text-align: center; line-height: 30px; font-size: 14px; color: var(--dark);
  }
  .pill-influence { left: 804px; width: 199px; }
  .pill-priority { left: 1046px; width: 121px; }

  .channel-card {
    position: absolute; left: 31px; width: 227px; height: 92px;
    border: 1px solid #c9dba0; border-radius: 4px; background: var(--white);
  }
  .card-management { top: 422px; }
  .card-stakeholders { top: 516px; }
  .card-team { top: 610px; }
  .card-icon { position: absolute; left: 21px; top: 8px; width: 50px; height: 54px; }
  .card-label { position: absolute; left: 2px; width: 88px; bottom: 7px; text-align: center; font-size: 9px; font-weight: 800; color: var(--ink); }
  .card-list { position: absolute; left: 92px; right: 12px; top: 3px; list-style: none; }
  .card-list li { display: flex; align-items: flex-end; height: 16.8px; font-size: 9px; font-weight: 800; color: var(--ink); }
  .card-list li::after { content: ""; flex: 1; border-bottom: 1.5px dotted var(--ink); margin-left: 1px; margin-bottom: 3px; }

  .grid-table {
    position: absolute; top: 393px; height: 311px;
    display: grid; grid-template-rows: 27px 1fr 1fr 1fr;
    border: 1px solid var(--rule);
  }
  .grid-table > div { border-right: 1px solid var(--rule); border-bottom: 1px solid var(--rule); }
  .grid-table .head { background: var(--white); display: flex; align-items: center; justify-content: center; font-size: 6.5px; font-weight: 800; color: var(--ink); }
  .grid-table .head svg { width: 20px; height: 16px; }
  .grid-table .shade { background: var(--cell-grey); }
  .grid-table .plain { background: var(--white); }
  .grid-table .last-col { border-right: none; }
  .grid-table .last-row { border-bottom: none; }
  .table-medium { left: 288px; width: 484px; grid-template-columns: repeat(6, 1fr); }
  .table-influence { left: 805px; width: 200px; grid-template-columns: repeat(4, 1fr); border-color: #bbbbbb; }
  .table-influence > div, .table-priority > div { border-color: #c4c4c4; }
  .table-priority { left: 1047px; width: 120px; grid-template-columns: repeat(3, 1fr); border-color: #bbbbbb; }

  .stage-band { position: absolute; left: 0; top: 730px; width: 1200px; height: 47px; background: var(--green); }
  .stage-label { position: absolute; top: 0; line-height: 47px; font-size: 19px; color: var(--dark); transform: translateX(-50%); }
  .stage-who { left: 141px; }
  .stage-what { left: 531px; }
  .stage-how { left: 903px; }
  .stage-when { left: 1106px; }
  .stage-dividers { position: absolute; left: 0; top: 0; width: 1200px; height: 47px; }

  .footer {
    position: absolute; left: 0; top: 779px; width: 1200px; height: 69px; background: var(--ink);
    color: var(--white); font-size: 14.5px; padding: 19px 0 0 33px; letter-spacing: 0.1px;
  }
</style>
</head>
<body>
<div class="canvas">

  <div class="title-tab">Project&nbsp; Communication Strategy Model</div>

  <div class="brand">
    <span class="brand-name">brindlecove</span>
    <span class="brand-mark"></span>
  </div>

  <svg class="connectors" viewBox="0 0 1200 848" aria-hidden="true">
    <g stroke="var(--green)" stroke-width="7" fill="none">
      <line x1="596" y1="155" x2="596" y2="212"/>
      <line x1="118" y1="229" x2="884" y2="229"/>
      <line x1="121" y1="226" x2="121" y2="284"/>
      <line x1="121" y1="320" x2="121" y2="400"/>
    </g>
    <polygon points="109,398 133,398 121,416" fill="var(--green)"/>
    <polygon points="596,204 622,229 596,255 570,229" fill="var(--dark)"/>
  </svg>

  <div class="flow-box flow-event">Event</div>
  <div class="flow-question">Reportable?</div>
  <div class="flow-box flow-yes">Yes</div>
  <div class="flow-box flow-no">No</div>
  <div class="flow-box flow-end">End</div>

  <div class="section-bar bar-channel">Channel</div>
  <div class="section-bar bar-medium">Medium</div>
  <div class="section-bar bar-delivery">Delivery</div>

  <div class="sub-pill pill-influence">Influencing Technique</div>
  <div class="sub-pill pill-priority">Priority</div>

  <!-- Channel cards -->
  <div class="channel-card card-management">
    <svg class="card-icon" viewBox="0 0 50 54" aria-hidden="true"><polygon points="25,2 48,26 34,26 34,52 16,52 16,26 2,26" fill="var(--green)"/></svg>
    <div class="card-label">Management</div>
    <ol class="card-list"><li>1)</li><li>2)</li><li>3)</li><li>4)</li><li>5)</li></ol>
  </div>
  <div class="channel-card card-stakeholders">
    <svg class="card-icon" viewBox="0 0 50 54" aria-hidden="true"><polygon points="48,27 24,4 24,18 2,18 2,36 24,36 24,50" fill="var(--green)"/></svg>
    <div class="card-label">Stakeholders</div>
    <ol class="card-list"><li>1)</li><li>2)</li><li>3)</li><li>4)</li><li>5)</li></ol>
  </div>
  <div class="channel-card card-team">
    <svg class="card-icon" viewBox="0 0 50 54" aria-hidden="true"><polygon points="25,52 48,28 34,28 34,2 16,2 16,28 2,28" fill="var(--green)"/></svg>
    <div class="card-label">Project Team</div>
    <ol class="card-list"><li>1)</li><li>2)</li><li>3)</li><li>4)</li><li>5)</li></ol>
  </div>

  <!-- Medium table -->
  <div class="grid-table table-medium">
    <div class="head" title="Email"><svg viewBox="0 0 20 16" aria-label="Email"><rect x="2" y="3" width="16" height="10" fill="none" stroke="var(--dark)" stroke-width="1.4"/><polyline points="2,3 10,9.5 18,3" fill="none" stroke="var(--dark)" stroke-width="1.4"/></svg></div>
    <div class="head" title="Phone"><svg viewBox="0 0 20 16" aria-label="Phone"><path d="M6 2 L8.5 2 L9.5 5.5 L8 7 Q9.5 10 12 11 L13.5 9.5 L17 10.5 L17 13 Q11 15 7.5 10.5 Q4.5 6.5 6 2 Z" fill="var(--dark)"/></svg></div>
    <div class="head" title="Meeting"><svg viewBox="0 0 20 16" aria-label="Meeting"><circle cx="6" cy="6" r="2" fill="var(--dark)"/><circle cx="14" cy="6" r="2" fill="var(--dark)"/><circle cx="10" cy="5" r="2.3" fill="var(--dark)"/><path d="M2 13 Q6 7.5 10 13 Z M10 13 Q14 7.5 18 13 Z M5.5 13 Q10 6.5 14.5 13 Z" fill="var(--dark)"/></svg></div>
    <div class="head" title="Presentation"><svg viewBox="0 0 20 16" aria-label="Presentation"><rect x="3" y="2" width="14" height="11" fill="none" stroke="var(--dark)" stroke-width="1.3"/><rect x="5" y="4" width="4" height="4" fill="var(--dark)"/><rect x="10.5" y="4" width="4.5" height="1.3" fill="var(--dark)"/><rect x="10.5" y="6.7" width="4.5" height="1.3" fill="var(--dark)"/><rect x="5" y="9.5" width="10" height="1.3" fill="var(--dark)"/></svg></div>
    <div class="head" title="Documents"><svg viewBox="0 0 20 16" aria-label="Documents"><path d="M2 3 L7.5 3 L9 4.5 L17 4.5 L17 13 L2 13 Z" fill="var(--dark)"/><path d="M3.5 7 L18.5 7 L17 13 L2 13 Z" fill="#555"/></svg></div>
    <div class="head last-col" title="Online"><svg viewBox="0 0 20 16" aria-label="Online"><rect x="4" y="2.5" width="12" height="8.5" fill="none" stroke="var(--dark)" stroke-width="1.4"/><rect x="1.5" y="12" width="17" height="1.8" fill="var(--dark)"/></svg></div>

    <div class="shade"></div><div class="shade"></div><div class="shade"></div><div class="shade"></div><div class="shade"></div><div class="shade last-col"></div>
    <div class="plain"></div><div class="plain"></div><div class="plain"></div><div class="plain"></div><div class="plain"></div><div class="plain last-col"></div>
    <div class="shade last-row"></div><div class="shade last-row"></div><div class="shade last-row"></div><div class="shade last-row"></div><div class="shade last-row"></div><div class="shade last-row last-col"></div>
  </div>

  <!-- Influencing technique table -->
  <div class="grid-table table-influence">
    <div class="head">Rational</div><div class="head">Emotional</div><div class="head">Consultation</div><div class="head last-col">Collaboration</div>
    <div class="shade"></div><div class="shade"></div><div class="shade"></div><div class="shade last-col"></div>
    <div class="plain"></div><div class="plain"></div><div class="plain"></div><div class="plain last-col"></div>
    <div class="shade last-row"></div><div class="shade last-row"></div><div class="shade last-row"></div><div class="shade last-row last-col"></div>
  </div>

  <!-- Priority table -->
  <div class="grid-table table-priority">
    <div class="head">High</div><div class="head">Medium</div><div class="head last-col">Low</div>
    <div class="shade"></div><div class="shade"></div><div class="shade last-col"></div>
    <div class="plain"></div><div class="plain"></div><div class="plain last-col"></div>
    <div class="shade last-row"></div><div class="shade last-row"></div><div class="shade last-row last-col"></div>
  </div>

  <!-- Stage band -->
  <div class="stage-band">
    <svg class="stage-dividers" viewBox="0 0 1200 47" aria-hidden="true">
      <g fill="none" stroke="var(--white)" stroke-width="6">
        <polyline points="262,-2 278,23.5 262,49"/>
        <polyline points="782,-2 798,23.5 782,49"/>
        <polyline points="1021,-2 1037,23.5 1021,49"/>
      </g>
    </svg>
    <span class="stage-label stage-who">Who</span>
    <span class="stage-label stage-what">What</span>
    <span class="stage-label stage-how">How</span>
    <span class="stage-label stage-when">When</span>
  </div>

  <footer class="footer">Brindlecove Communications Pty. Ltd / www.brindlecovecomms.example / PO Box 418, Harbourview NSW 2000 / +61 2 5550 0148&nbsp; ABN: 00 123 456 789</footer>

</div>
</body>
</html>
```